Luxury Toilet Rental Business. Tallowby Hire.

Tallowby Hire (the logo is in the uploaded files)
We RENT and SELL Luxury Trailer toilets.
- Show location, number, pricing, pictures.
- We have two stall trailers for rent AND 3 stall trailers
- We sell them too
- We want our phone number shown
- We are a local company
- Slogan: Brighten your gathering with Tallowby Hire. The Velvet Privy
- We want a pricing portion
- We want the sizes shown
- We want the different rates/ prices shown
- We do 1 day rentals
- We do 1 week rentals
- We want the service area. We serve Los Angeles County, Orange County, Riverside County, San Bernardino County, and Palm Desert.
- Our location is in Fernvale California

Target Market(s)

Event planners, wedding planners, venue planners, concerts, events, gatherings.

Industry/Entity Type

Luxury Toilet Rentals

Number of Pages Required

1 page

Font styles to use
Serif
Sans Serif

Colors
EE7325
F08F49
F5BC92
FAE3D3
FDF4ED

Requirements
Must have
• Location, pricing, pictures, available areas. Our slogan.
Nice to have
• I like the idea of having tabs that show price, a tab that shows our contact information, pictures, event ideas, and where we service (the areas we'll go to)

```html
<!DOCTYPE html>
<html lang="en">
<head>
<meta charset="UTF-8">
<title>Tallowby Hire – Luxury Trailer Toilets</title>
<link href="https://fonts.googleapis.com/css2?family=Poppins:wght@400;500;600;700;800&display=swap" rel="stylesheet">
<style>
:root{
  --orange:#EE7325;
  --orange-mid:#F08F49;
  --peach:#F5BC92;
  --blush:#FAE3D3;
  --cream:#FDF4ED;
  --ink:#1f1f1f;
  --text:#555;
  --white:#fff;
}
*{box-sizing:border-box;margin:0;padding:0}
html,body{width:1200px;height:4400px;overflow:hidden}
body{font-family:'Poppins',sans-serif;color:var(--ink);background:var(--white);position:relative}
.section{position:absolute;left:0;width:1200px}
.ph{position:absolute;border-radius:4px}
p{font-size:15px;line-height:1.75;color:var(--text)}
.btn{display:inline-block;background:var(--orange);color:var(--white);font-size:13px;font-weight:500;padding:7px 20px;border-radius:4px}
.eyebrow{font-size:30px;font-weight:800;color:var(--orange);letter-spacing:1px}
.sub{font-size:19px;font-weight:700;letter-spacing:2px;color:var(--ink)}
.rule{display:flex;align-items:center;gap:0}
.rule span{display:block;height:2px;background:var(--ink)}
.rule i{display:block;width:12px;height:12px;background:var(--ink);transform:rotate(45deg)}

/* header / hero */
.hero{top:0;height:740px}
.hero-photo{left:0;top:0;width:1200px;height:740px;border-radius:0;background:linear-gradient(180deg,#c9ccd0 0%,#a9adb2 45%,#8d8f90 75%,#6f6d6a 100%)}
.nav{position:absolute;left:0;top:0;width:1200px;height:64px;background:rgba(255,255,255,.92);display:flex;align-items:center;padding:0 112px}
.logo{font-size:26px;font-weight:800;color:var(--orange);letter-spacing:1px;display:flex;align-items:center;gap:10px}
.logo b{display:block;width:14px;height:14px;background:var(--orange)}
.nav-links{margin-left:auto;display:flex;gap:26px;align-items:center;font-size:14px;font-weight:500}
.nav-links .btn{padding:6px 16px}
.hero-card{position:absolute;left:600px;top:380px;width:488px;height:260px;background:var(--orange);border-radius:26px;display:flex;align-items:center;justify-content:center;text-align:center;color:var(--white);font-size:33px;font-weight:700;line-height:1.55;padding:0 30px}

/* about */
.about{top:740px;height:600px}
.about .eyebrow{position:absolute;left:112px;top:84px}
.about .rule{position:absolute;left:310px;top:104px}
.about .sub{position:absolute;left:112px;top:134px;font-size:17px}
.about .copy{position:absolute;left:112px;top:176px;width:460px}
.about .copy p+p{margin-top:14px}
.about .btn{margin-top:16px}
.about .ph-main{left:812px;top:80px;width:276px;height:380px;background:linear-gradient(180deg,#7fb3e0,#c7dde8 55%,#a8b28a)}
.about .ph-inset{left:628px;top:190px;width:232px;height:318px;background:linear-gradient(160deg,#e9e4dc,#cbbfb0);border:4px solid var(--white)}

/* gallery */
.gallery{top:1340px;height:840px;background:var(--cream)}
.gallery .eyebrow{position:absolute;left:112px;top:80px}
.gallery .sub{position:absolute;left:112px;top:140px}
.gallery .intro{position:absolute;left:700px;top:62px;width:388px;font-size:14px}
.tile{position:absolute}
.tile .ph{inset:0}
.size{position:absolute;left:50%;bottom:14px;transform:translateX(-50%);background:var(--orange);color:var(--white);font-size:14px;padding:6px 18px;white-space:nowrap}
.g1{left:112px;top:220px;width:300px;height:310px}
.g2{left:444px;top:220px;width:644px;height:310px}
.g3{left:112px;top:560px;width:300px;height:262px}
.g4{left:444px;top:560px;width:308px;height:262px}
.g5{left:784px;top:560px;width:304px;height:262px}

/* rent & sell band */
.band{top:2250px;height:520px}
.band .ph{left:560px;top:0;width:640px;height:520px;border-radius:0;background:linear-gradient(180deg,#dfe6ec,#a7acb0 60%,#7d7b78)}
.band svg{position:absolute;left:0;top:0}
.band .title{position:absolute;left:112px;top:140px;color:var(--white);font-size:30px;font-weight:800;line-height:1.3;letter-spacing:1px}
.band .copy{position:absolute;left:112px;top:232px;width:380px;color:var(--white);font-size:14px}
.band .outline{position:absolute;left:112px;top:310px;border:1.5px solid var(--white);color:var(--white);background:transparent;font-size:13px;padding:5px 18px;border-radius:4px}

/* pricing */
.pricing{top:2840px;height:560px}
.pricing .ph{left:112px;top:12px;width:444px;height:480px;background:linear-gradient(160deg,#d9b796,#f1e4d2 45%,#a77a55)}
.pricing .eyebrow{position:absolute;left:588px;top:14px}
.pricing .sub{position:absolute;left:588px;top:60px;font-size:17px}
.pricing .copy{position:absolute;left:588px;top:102px;width:500px}
.rates{position:absolute;left:588px;top:260px;display:flex;gap:24px}
.rate{white-space:nowrap}
.rate+.rate{border-left:2px solid var(--ink);padding-left:24px}
.rate .we{font-size:17px;font-weight:500}
.rate .plan{font-size:28px;font-weight:600;color:var(--orange);line-height:1.25}
.rate .cost{font-size:13px;margin-top:6px}
.rate .cost u{margin-left:12px;font-weight:600}
.pricing .btn{position:absolute;left:588px;top:392px}

/* service area */
.service{top:3440px;height:232px;background:var(--cream)}
.service .head{position:absolute;left:0;top:40px;width:1200px;display:flex;justify-content:center;align-items:center;gap:20px}
.service .eyebrow{font-size:28px}
.service .sub{position:absolute;left:0;top:90px;width:1200px;text-align:center;font-size:17px}
.tabs{position:absolute;left:112px;top:148px;display:flex;gap:22px}
.tab{width:180px;height:40px;border:1.5px solid #777;display:flex;align-items:center;justify-content:center;font-size:14px;background:var(--white)}
.tab.active{background:var(--orange);border-color:var(--orange);color:var(--white)}
.map{top:3672px;height:368px;background:linear-gradient(135deg,#eceae6,#dfe3e6 50%,#e8e2d8)}

/* footer */
.footer{top:4040px;height:360px;background:var(--orange);color:var(--white)}
.footer .logo{position:absolute;left:112px;top:60px;color:var(--white)}
.footer .logo b{background:var(--white)}
.footer .blurb{position:absolute;left:112px;top:150px;width:300px;color:var(--white);font-size:14px;line-height:1.6}
.fcol{position:absolute;top:50px}
.fcol h4{font-size:17px;font-weight:700;letter-spacing:1px;margin-bottom:14px}
.fcol li{list-style:none;font-size:13px;line-height:1.9;display:flex;align-items:center;gap:10px}
.c1{left:456px}.c2{left:740px}.c3{left:956px}
.copyright{position:absolute;left:0;bottom:26px;width:1200px;text-align:center;font-size:13px}
.fine{position:absolute;right:40px;bottom:26px;font-size:12px}
</style>
</head>
<body>

<header class="section hero">
  <div class="ph hero-photo" role="img" aria-label="Grey luxury trailer toilet with steps parked in a paved lot"></div>
  <nav class="nav">
    <div class="logo"><b></b>TALLOWBY</div>
    <div class="nav-links">
      <span>Events</span><span>Gallery</span><span>Service Area</span><span>Pricing</span>
      <span class="btn">Contact Us</span>
    </div>
  </nav>
  <div class="hero-card">Brighten your gathering with Tallowby Hire. The Velvet Privy</div>
</header>

<section class="section about">
  <h2 class="eyebrow">ABOUT US</h2>
  <div class="rule"><span style="width:140px"></span><i></i><span style="width:50px"></span></div>
  <h3 class="sub">WE ARE A LOCAL COMPANY</h3>
  <div class="copy">
    <p>Lorem ipsum dolor sit amet, consectetur adipiscing elit, sed do eiusmod tempor incididunt ut labore et dolore magna aliqua. Quis ipsum suspendisse ultrices gravida. Risus commodo viverra maecenas accumsan lacus vel facilisis.</p>
    <p>Lorem ipsum dolor sit amet, consectetur adipiscing elit, sed do eiusmod tempor incididunt ut labore et</p>
    <span class="btn">Read More</span>
  </div>
  <div class="ph ph-main" role="img" aria-label="Trailer toilet parked outdoors under blue sky"></div>
  <div class="ph ph-inset" role="img" aria-label="Bright trailer restroom interior with sink and plant"></div>
</section>

<section class="section gallery">
  <h2 class="eyebrow">OUR GALLERY</h2>
  <h3 class="sub">LOREM IPSUM DOLOR SIT</h3>
  <p class="intro">Lorem ipsum dolor sit amet, consectetur adipiscing elit, sed do eiusmod tempor incididunt ut labore et dolore magna aliqua. Quis ipsum suspendisse ut lacus gravida. Risus commodo viverra.</p>
  <div class="tile g1"><div class="ph" role="img" aria-label="White restroom sink interior" style="background:linear-gradient(160deg,#f2f2f2,#c9cccf)"></div><span class="size">Size : 50 Sq.ft</span></div>
  <div class="tile g2"><div class="ph" role="img" aria-label="White two-stall luxury trailer toilet" style="background:linear-gradient(160deg,#5a5a5d,#2e2f32 50%,#c6c8ca)"></div><span class="size">Size : 50 Sq.ft</span></div>
  <div class="tile g3"><div class="ph" role="img" aria-label="Restroom stall interior" style="background:linear-gradient(160deg,#e4e4e2,#b7b9bb)"></div><span class="size">Size : 50 Sq.ft</span></div>
  <div class="tile g4"><div class="ph" role="img" aria-label="Grey three-stall trailer in a yard" style="background:linear-gradient(160deg,#9ea3a7,#5f6368)"></div><span class="size">Size : 50 Sq.ft</span></div>
  <div class="tile g5"><div class="ph" role="img" aria-label="White vessel sink on counter" style="background:linear-gradient(160deg,#f4f4f4,#bfc3c6)"></div><span class="size">Size : 50 Sq.ft</span></div>
</section>

<section class="section band">
  <div class="ph" role="img" aria-label="Grey luxury trailer toilet with folding steps outside a building"></div>
  <svg width="700" height="520" viewBox="0 0 700 520" aria-hidden="true">
    <polygon points="0,0 660,0 560,520 0,520" fill="var(--orange)"/>
  </svg>
  <h2 class="title">WE RENT &amp; SELL<br>LUXURY TRAILER TOILETS</h2>
  <p class="copy">Lorem ipsum dolor sit amet, consectetur adipiscing elit, sed do eiusmod tempor incididunt ut labore et</p>
  <span class="outline">Rent Now</span>
</section>

<section class="section pricing">
  <div class="ph" role="img" aria-label="Warm lit restroom with round mirror and vanity"></div>
  <h2 class="eyebrow">RENTAL PRICE</h2>
  <h3 class="sub">LOREM IPSUM DOLOR SIT</h3>
  <p class="copy">Lorem ipsum dolor sit amet, consectetur adipiscing elit, sed do eiusmod tempor incididunt ut labore et dolore magna aliqua. Quis ipsum suspendisse ultrices gravida. Risus commodo viverra maecenas accumsan lacus vel facilisis.</p>
  <div class="rates">
    <div class="rate"><div class="we">We Do</div><div class="plan">1 Day Rentals</div><div class="cost">$ 205.95 / <u>View More</u></div></div>
    <div class="rate"><div class="we">We Do</div><div class="plan">1 Week Rentals</div><div class="cost">$ 205.95 / <u>View More</u></div></div>
  </div>
  <span class="btn">Book Now</span>
</section>

<section class="section service">
  <div class="head">
    <div class="rule"><span style="width:150px"></span><i></i></div>
    <h2 class="eyebrow">WHERE WE SERVICE</h2>
    <div class="rule"><i></i><span style="width:150px"></span></div>
  </div>
  <h3 class="sub">LOREM IPSUM DOLOR SIT</h3>
  <div class="tabs">
    <div class="tab active">Los Angeles</div>
    <div class="tab">San Bernardino</div>
    <div class="tab">Orange</div>
    <div class="tab">Riverside</div>
    <div class="tab">Palm Desert</div>
  </div>
</section>

<div class="section map" role="img" aria-label="Street map of the Fernvale service area"></div>

<footer class="section footer">
  <div class="logo"><b></b>TALLOWBY</div>
  <p class="blurb">Lorem ipsum dolor sit amet, consectetur adipiscing elit, sed do eiusmod tempor incididunt ut</p>
  <div class="fcol c1">
    <h4>COMPANY DETAIL</h4>
    <ul>
      <li><svg width="12" height="14" viewBox="0 0 12 14"><path d="M6 0a5 5 0 0 0-5 5c0 4 5 9 5 9s5-5 5-9a5 5 0 0 0-5-5zm0 7a2 2 0 1 1 0-4 2 2 0 0 1 0 4z" fill="#fff"/></svg>Fernvale California</li>
      <li><svg width="12" height="12" viewBox="0 0 12 12"><path d="M2.5 0l2 3-1.3 1.3a7 7 0 0 0 4.5 4.5L9 7.5l3 2-1 2.5C5 12 0 7 0 1z" fill="#fff"/></svg>(714) 555-0148</li>
      <li><svg width="13" height="10" viewBox="0 0 13 10"><rect width="13" height="10" rx="1" fill="#fff"/><path d="M0 1l6.5 5L13 1" stroke="#EE7325" fill="none"/></svg>hello@tallowbyhire.com</li>
    </ul>
  </div>
  <div class="fcol c2">
    <h4>QUICK LINKS</h4>
    <ul><li>Events</li><li>Gallery</li><li>Service Area</li><li>Pricing</li><li>Contact Us</li></ul>
  </div>
  <div class="fcol c3">
    <h4>SUPPORT</h4>
    <ul><li>FAQs</li><li>Help Center</li><li>Privacy Policy</li><li>Cookie Policy</li><li>Sitemaps</li></ul>
  </div>
  <div class="copyright">Copyright 2024 Tallowby Hire. All Rights Reserved.</div>
  <div class="fine">1/1</div>
</footer>

</body>
</html>
```